Northfield Builders Guild Business card

We are looking for a new business card design with photo included.
Our business is a nonprofit construction contractor membership organization. We offer business education, assist with business setup and licensing, provide safety training, and provide a member directory.
URL: www.builderslinkguild.org
Color code:
CMYK: 0 cyan, 42 magenta, 100 yellow, 0 black for Print.
Hexidecimal: #FF9900
RGB: R 255; G 153; B 0

```html
<!DOCTYPE html>
<html lang="en">
<head>
<meta charset="utf-8">
<title>Northfield Builders Guild – Business Card</title>
<link rel="stylesheet" href="https://fonts.googleapis.com/css2?family=Montserrat:wght@400;800&family=Open+Sans:wght@400&display=swap">
<style>
  :root {
    --brand-orange: #ff9900;
    --charcoal: #333333;
    --card-white: #ffffff;
    --backdrop: #262626;
    --text-muted: #444444;
  }
  * { margin: 0; padding: 0; box-sizing: border-box; }
  html, body { width: 1200px; height: 795px; overflow: hidden; }
  body {
    background: var(--backdrop);
    font-family: "Open Sans", sans-serif;
    position: relative;
  }
  .card {
    position: absolute;
    top: 248px;
    width: 520px;
    height: 300px;
    background: var(--card-white);
    border-radius: 20px;
    overflow: hidden;
  }
  .card--front { left: 53px; }
  .card--back { left: 627px; }

  .brand-name {
    font-family: "Montserrat", sans-serif;
    font-weight: 800;
    color: var(--charcoal);
    text-transform: uppercase;
    line-height: 1.05;
    display: flex;
    align-items: center;
    gap: 10px;
  }
  .brand-mark {
    width: 14px;
    height: 14px;
    background: var(--brand-orange);
    flex: none;
  }
  .card--front .brand-name {
    position: absolute;
    left: 34px;
    top: 118px;
    font-size: 19px;
  }
  .card--back .brand-name {
    position: absolute;
    left: 0; right: 0; top: 0; bottom: 0;
    justify-content: center;
    font-size: 30px;
  }
  .card--back .brand-mark { width: 22px; height: 22px; }

  .divider {
    position: absolute;
    left: 262px;
    top: 62px;
    width: 1px;
    height: 138px;
    background: var(--brand-orange);
  }
  .contact {
    position: absolute;
    left: 286px;
    top: 64px;
  }
  .contact__name {
    font-family: "Montserrat", sans-serif;
    font-weight: 400;
    color: var(--brand-orange);
    font-size: 15px;
    letter-spacing: 3px;
    text-transform: uppercase;
  }
  .contact__title {
    font-size: 10px;
    color: var(--text-muted);
    margin-top: 2px;
  }
  .contact__lines {
    list-style: none;
    margin-top: 30px;
  }
  .contact__lines li {
    display: flex;
    align-items: center;
    gap: 8px;
    font-size: 13.5px;
    color: var(--charcoal);
    line-height: 22px;
  }
  .contact__lines svg { width: 12px; height: 12px; flex: none; }
  .edge-band {
    position: absolute;
    left: 0; top: 0;
    width: 520px; height: 300px;
  }
</style>
</head>
<body>
  <section class="card card--front" aria-label="Business card front">
    <svg class="edge-band" viewBox="0 0 520 300" aria-hidden="true">
      <polygon points="0,263 290,263 318,219 326,219 294,271 0,271" fill="var(--charcoal)"/>
      <polygon points="0,280 302,280 330,236 520,236 520,300 0,300" fill="var(--brand-orange)"/>
    </svg>
    <div class="brand-name"><span class="brand-mark"></span><span>Northfield<br>Builders Guild</span></div>
    <div class="divider"></div>
    <div class="contact">
      <p class="contact__name">Daniel Reyes</p>
      <p class="contact__title">CEO/Managing Director</p>
      <ul class="contact__lines">
        <li>
          <svg viewBox="0 0 12 12" aria-hidden="true"><path d="M2.5 1 L4.5 1 L5.2 3.6 L4 4.5 C4.6 6 6 7.4 7.5 8 L8.4 6.8 L11 7.5 L11 9.5 C11 10.3 10.3 11 9.5 11 C5 11 1 7 1 2.5 C1 1.7 1.7 1 2.5 1 Z" fill="var(--brand-orange)"/></svg>
          <span>555-014-7730</span>
        </li>
        <li>
          <svg viewBox="0 0 12 12" aria-hidden="true"><rect x="0.5" y="2" width="11" height="8" fill="var(--brand-orange)"/><polyline points="0.5,2 6,6.5 11.5,2" fill="none" stroke="#fff" stroke-width="1"/></svg>
          <span>dreyes@builderslinkguild.org</span>
        </li>
      </ul>
    </div>
  </section>

  <section class="card card--back" aria-label="Business card back">
    <div class="brand-name"><span class="brand-mark"></span><span>Northfield<br>Builders Guild</span></div>
  </section>
</body>
</html>
```